Flat Belly Design Graphics for Social

I want to create 9 social media graphics (new Instagram size 4:5 (1080 x 1350 pixels) focusing on our Flat Belly Graphics, using the pics attached. Use the attached pics, NO RANDOM STOCK PHOTOGRAPHY. For the color scheme of the graphics, the color palette is attached. YOU MUST POST ALL 9 GRAPHICS IN ONE ENTRY.
Using the 3 titles below, create one set of graphics. 1) with all text, then for the others, use the pictures as detailed below in IMPORTANT:
1. Ten-Week Bright Morning Reboot
2. The Quick Garden Kitchen Menu Guide
3. Studio Habits for Lasting Energy Past Midlife - Zero Gym Needed
IMPORTANT:
Only use RK Pic 1 and RK Pic 2 with the title, Ten-Week Bright Morning Reboot
Only use meal plan1 and meal plan2 pics with the title, Quick Garden Kitchen Menu Guide
Only use studio habits 1 and studio habits 2 pics with the title, Studio Habits for Lasting Energy Past Midlife - Zero Gym Needed
women over 40

```html
<!DOCTYPE html>
<html lang="en">
<head>
<meta charset="utf-8">
<title>Bright Morning Social Set</title>
<link rel="stylesheet" href="https://fonts.googleapis.com/css2?family=Anton&family=Allura&family=Montserrat:wght@400;600;700&family=Outfit:wght@700;800&display=swap">
<style>
  :root {
    --page: #ffffff;
    --band: #e39aae;
    --card: #fbecee;
    --teal: #4a9086;
    --forest: #1f4c44;
    --rose: #e27b9b;
    --rose-soft: #ea9fb5;
    --ink: #111111;
  }
  * { margin: 0; padding: 0; box-sizing: border-box; }
  html, body { width: 840px; height: 1200px; overflow: hidden; background: var(--page); }
  .canvas { position: relative; width: 840px; height: 1200px; }
  .set-label, .closing-note {
    position: absolute; left: 0; width: 840px; text-align: center;
    font-family: "Outfit", sans-serif; font-weight: 800; color: var(--ink);
  }
  .set-label { top: 78px; font-size: 22px; }
  .closing-note { top: 1104px; font-size: 22px; }

  .post {
    position: absolute; width: 237px; height: 296px; overflow: hidden;
    background: var(--card);
    border-top: 12px solid var(--band); border-bottom: 12px solid var(--band);
  }
  .post > * { position: absolute; }
  .col-1 { left: 58px; } .col-2 { left: 303px; } .col-3 { left: 549px; }
  .row-1 { top: 149px; } .row-2 { top: 455px; } .row-3 { top: 760px; }

  .title {
    font-family: "Anton", sans-serif; text-transform: uppercase;
    color: var(--forest); line-height: 1.22; letter-spacing: 0.2px; white-space: nowrap;
  }
  .title .accent { color: var(--teal); }
  .script {
    font-family: "Allura", cursive; color: var(--rose-soft);
    transform: rotate(-9deg); white-space: nowrap; line-height: 1;
  }
  .byline { font-family: "Montserrat", sans-serif; color: var(--forest); }
  .byline strong { display: block; font-size: 9px; font-weight: 700; }
  .byline span { display: block; font-size: 5px; margin-top: 1px; }
  .tagline {
    font-family: "Montserrat", sans-serif; font-weight: 700; font-size: 6.5px;
    color: var(--forest); white-space: nowrap;
  }
  .tagline.rose { color: var(--rose); }
  .tagline.marked { background: var(--teal); color: var(--forest); padding: 0 1px; }
  .photo { display: block; }
  .photo-portrait { background: linear-gradient(160deg, #c9a38c 0%, #f3ece8 55%, #2a2624 100%); }
  .photo-portrait-wall { background: linear-gradient(180deg, #6b4a3a 0%, #d8c7bd 45%, #f2eeea 70%, #232020 100%); }
  .photo-table { background: linear-gradient(135deg, #7c5a3e 0%, #b9a47a 40%, #e9e5dc 60%, #4e3526 100%); }
  .photo-produce { background: radial-gradient(circle at 50% 50%, #efece6 0 18%, #3b2a21 40%, #7d6a2c 70%, #b4462f 100%); }
  .photo-friends-pink { background: linear-gradient(180deg, #e39aae 0%, #b07a66 50%, #efe2dc 100%); }
  .photo-friends { background: linear-gradient(170deg, #fbecee 0%, #c89a83 35%, #8fb6cf 75%, #fbecee 100%); }

  .sub-head { font-family: "Anton", sans-serif; color: var(--rose-soft); font-size: 12.5px; white-space: nowrap; }
  .copy { font-family: "Montserrat", sans-serif; color: var(--rose-soft); font-size: 6.4px; line-height: 1.4; }
  .copy.fine { font-size: 4.8px; }
  .hidden-reason {
    font-family: "Montserrat", sans-serif; font-weight: 700; font-size: 7px;
    color: var(--rose); text-decoration: underline; line-height: 1.45;
  }
</style>
</head>
<body>
<main class="canvas">
  <p class="set-label">Fixed</p>

  <!-- Row 1 -->
  <section class="post col-1 row-1">
    <div class="photo photo-portrait" role="img" aria-label="Smiling woman in a white cropped sweater and black trousers, pointing down" style="left:12px; top:86px; width:132px; height:222px;"></div>
    <h2 class="title" style="left:24px; top:18px; font-size:27px;"><span class="accent">Ten-Week</span> Bright<br>Morning</h2>
    <p class="script" style="left:84px; top:96px; font-size:44px;">Reboot!</p>
    <div class="byline" style="left:120px; top:234px;"><strong>By RK Hollis,</strong><span>#1 National Bestselling Author</span></div>
  </section>

  <section class="post col-2 row-1">
    <div class="photo photo-table" role="img" aria-label="Meal plan sheet on a wooden table with bowls of chicken, berries, grains and asparagus" style="left:0; top:0; width:237px; height:97px;"></div>
    <h2 class="title" style="left:13px; top:102px; font-size:25px;"><span class="accent">The Quick</span> Garden<br>Kitchen Menu</h2>
    <p class="script" style="left:14px; top:170px; font-size:40px;">Guide!</p>
    <p class="tagline" style="left:0; width:237px; text-align:center; top:250px;">Healthy, Delicious, and Simple.</p>
  </section>

  <section class="post col-3 row-1">
    <div class="photo photo-friends-pink" role="img" aria-label="Woman whispering a secret to a surprised friend" style="left:0; top:0; width:237px; height:109px;"></div>
    <h2 class="title" style="left:23px; top:120px; font-size:24px;"><span class="accent">Studio</span> Habits for<br>Lasting Energy</h2>
    <p class="script" style="left:72px; top:186px; font-size:36px;">Past Midlife!</p>
    <p class="tagline rose" style="left:0; width:237px; text-align:center; top:250px;">Zero Gym Needed!</p>
  </section>

  <!-- Row 2 -->
  <section class="post col-1 row-2">
    <div class="photo photo-portrait-wall" role="img" aria-label="Portrait of a smiling woman in a white cropped sweater" style="left:9px; top:-12px; width:97px; height:296px;"></div>
    <h2 class="title" style="left:118px; top:12px; font-size:21px;"><span class="accent">Ten-Week</span><br>Bright<br>Morning</h2>
    <p class="script" style="left:162px; top:82px; font-size:28px;">Reboot!</p>
    <p class="hidden-reason" style="left:118px; top:138px; width:100px;">THE HIDDEN REASON YOU CAN'T LOSE THE BELLY FAT</p>
    <div class="byline" style="left:118px; top:242px;"><strong>By RK Hollis,</strong><span>#1 National Bestselling Author</span></div>
  </section>

  <section class="post col-2 row-2">
    <h2 class="title" style="left:38px; top:2px; font-size:19px; line-height:1.4;"><span class="accent">The Quick</span> Garden<br>Kitchen Menu</h2>
    <p class="script" style="left:130px; top:30px; font-size:30px;">Guide!</p>
    <div class="photo photo-produce" role="img" aria-label="Spiral meal plan notebook surrounded by fresh vegetables, fruit and grains on dark wood" style="left:0; top:61px; width:237px; height:235px;"></div>
    <p class="tagline marked" style="left:69px; top:250px;">Healthy, Delicious, and Simple.</p>
  </section>

  <section class="post col-3 row-2">
    <div class="photo photo-friends" role="img" aria-label="Two women, one whispering to the other who looks delighted" style="left:10px; top:50px; width:227px; height:246px;"></div>
    <h2 class="title" style="left:13px; top:12px; font-size:17px;"><span class="accent">Studio</span> Habits<br>for Lasting Energy</h2>
    <p class="script" style="left:10px; top:54px; font-size:22px;">Past Midlife!</p>
    <p class="tagline marked" style="left:23px; top:250px;">Zero Gym Needed!</p>
  </section>

  <!-- Row 3 -->
  <section class="post col-1 row-3">
    <h2 class="title" style="left:24px; top:12px; font-size:26px; line-height:1.25;">The Bright<br>Morning<br><span class="accent">Formula</span></h2>
    <p class="sub-head" style="left:24px; top:126px;">Sub Headline Here</p>
    <p class="copy" style="left:24px; top:148px; width:192px;">Lorem ipsum dolor sit amet, consectetur adipiscing elit, sed do eiusmod tempor incididunt ut labore dan dolore magna aliqua. Ut enim ad minim veniam, quis nostrud exeritation ullamco laboris nisi ut aliquip ex ea commodo consequat. Duis aute irure dolor in reprehenderit in voluptate velit esse cillum dolore eu fugiat nulla pariatur. Pengecualian sint occaecat cupidatat non proident, sunt in culpa qui officia deserunt mollit anim id est laborum.</p>
    <div class="byline" style="left:24px; top:244px;"><strong>By RK Hollis,</strong><span>#1 National Bestselling Author</span></div>
  </section>

  <section class="post col-2 row-3">
    <h2 class="title" style="left:0; width:237px; text-align:center; top:12px; font-size:18px;">Done - For - <span class="accent">You</span></h2>
    <p class="byline" style="left:0; width:237px; text-align:center; top:38px; font-size:11px; font-weight:700; letter-spacing:0.4px;">GARDEN KITCHEN MENU GUIDE</p>
    <p class="sub-head" style="left:37px; top:70px;">Sub Headline Here</p>
    <p class="copy" style="left:37px; top:90px; width:164px;">Lorem ipsum dolor sit amet, consectetur adipiscing elit, sed do eiusmod tempor incididunt ut labore dan dolore magna aliqua. Ut enim ad minim veniam, quis nostrud exeritation ullamco laboris nisi ut aliquip ex ea commodo consequat.</p>
    <p class="sub-head" style="left:37px; top:162px;">Third Headline Here</p>
    <p class="copy" style="left:37px; top:182px; width:164px;">Lorem ipsum dolor sit amet, consectetur adipiscing elit, sed do eiusmod tempor incididunt ut labore dan dolore magna aliqua. Ut enim ad minim veniam, quis nostrud exeritation ullamco laboris nisi ut aliquip ex ea commodo consequat.</p>
    <p class="tagline" style="left:0; width:237px; text-align:center; top:250px;">Healthy, Delicious, and Simple.</p>
  </section>

  <section class="post col-3 row-3">
    <h2 class="title" style="left:24px; top:10px; font-size:30px; text-transform:none;">Head<span class="accent">line</span></h2>
    <p class="copy" style="left:24px; top:60px; width:192px;">Lorem ipsum dolor sit amet, consectetur adipiscing elit, sed do eiusmod tempor incididunt ut labore dan dolore magna aliqua. Ut enim ad minim veniam, quis nostrud exeritation ullamco laboris nisi ut aliquip ex ea commodo consequat. Duis aute irure dolor in reprehenderit in voluptate velit esse cillum dolore eu fugiat nulla pariatur. Pengecualian sint occaecat cupidatat non proident, sunt in culpa qui officia deserunt mollit anim id est laborum.</p>
    <p class="sub-head" style="left:24px; top:146px; font-size:15px;">Sub Headline</p>
    <p class="copy fine" style="left:24px; top:168px; width:78px;">Lorem ipsum dolor sit amet, consectetur adipiscing elit, sed do eiusmod tempor incididunt ut labore dan dolore magna aliqua. Ut enim ad minim veniam, quis nostrud exeritation ullamco laboris nisi ut aliquip ex ea commodo consequat.</p>
    <p class="sub-head" style="left:133px; top:146px; font-size:15px;">Sub Headline</p>
    <p class="copy fine" style="left:133px; top:168px; width:78px;">Lorem ipsum dolor sit amet, consectetur adipiscing elit, sed do eiusmod tempor incididunt ut labore dan dolore magna aliqua. Ut enim ad minim veniam, quis nostrud exeritation ullamco laboris nisi ut aliquip ex ea commodo consequat.</p>
    <p class="tagline" style="left:24px; top:250px;">Zero Gym Needed!</p>
  </section>

  <p class="closing-note">Hi! I'd love to hear your feedback to my design!</p>
</main>
</body>
</html>
```